Desktop and Networking Support Course 9.17.25

Important the ad should not be very busy with the text taking up the major part of the ad .. please do not make the text so big that it takes up most of the ad..
Flyer Design Brief for Graphic Artist
also i am looking for something unique or creative that it will stand out .
Size & Layout:
Full Page with Bleed: 8” x 10.75” + 0.25” bleed on all sides.
Footer Space: Leave a 1-inch margin at the bottom for footer content (e.g., contact info, logo, or call-to-action).
Target Audience:
College-age students (around 24 years old)
Located in the USA
Interested in creative, professional, and career-building opportunities
Purpose:
To attract students to enroll in a college program
Flyer should be eye-catching, unique, and creative
Text must be clear and readable,
Design Style:
Use vector art, typography, or photography — your choice
If using photography, feature a white young professional USA citizen:
Wearing a white collared shirt
not with long hair
Creative Direction:
The flyer should stand out visually — something people would want to look at and keep
Showcase creativity and professionalism
Use bold colors, dynamic layout, or unexpected design elements to grab attention
Avoid clutter — keep the design balanced and clean
Text Suggestions (can be adjusted):
Footer,
please leave one inch on the bottom for the footer

```html
<!DOCTYPE html>
<html lang="en">
<head>
<meta charset="utf-8">
<title>Desktop &amp; Network Support Course Flyer</title>
<link href="https://fonts.googleapis.com/css2?family=Anton&family=Red+Hat+Display:wght@500;700;800&display=swap" rel="stylesheet">
<style>
  :root{
    --navy-deep:#141a3c;
    --navy:#1c1f5a;
    --royal:#2c4fa3;
    --sky:#4fa3de;
    --yellow:#f4f01a;
    --white:#ffffff;
    --ink:#1b2152;
    --stage:#e4e4e6;
  }
  *{margin:0;padding:0;box-sizing:border-box}
  html,body{width:1200px;height:1117px;overflow:hidden;background:var(--stage)}
  .flyer{position:absolute;left:188px;top:10px;width:823px;height:1097px;background:var(--navy);overflow:hidden;font-family:"Red Hat Display",sans-serif;color:var(--white)}
  .hero-bg{position:absolute;left:0;top:0;width:823px;height:422px}
  .mid-band{position:absolute;left:0;top:422px;width:823px;height:193px;background:linear-gradient(90deg,#e9eaee,#fafafa 50%,#e9eaee)}
  .lower-bg{position:absolute;left:0;top:615px;width:823px;height:329px;background:linear-gradient(180deg,#1c1f5a,#22266a)}
  .tagline{position:absolute;left:0;top:60px;width:823px;text-align:center;font-family:"Anton",sans-serif;font-size:47px;letter-spacing:0.2px;line-height:62px;white-space:nowrap}
  .tagline .accent{color:var(--sky);position:relative;padding:0 10px}
  .tagline svg{position:absolute;left:-8px;top:-12px;width:262px;height:88px;overflow:visible}
  .title-box{position:absolute;left:99px;top:154px;width:625px;height:170px;border-radius:18px;background:linear-gradient(90deg,#2b4ea3,#4b8fd4 50%,#2b4ea3);box-shadow:0 8px 12px rgba(0,0,0,.35);display:flex;align-items:center;justify-content:center}
  .title-box h1{font-family:"Anton",sans-serif;font-weight:400;font-size:71px;line-height:68px;text-align:center;letter-spacing:.5px;text-shadow:0 3px 4px rgba(0,0,0,.3);white-space:nowrap}
  .subtitle{position:absolute;left:0;top:340px;width:823px;text-align:center;color:var(--yellow);font-size:27px;font-weight:500}
  .stat-box{position:absolute;left:99px;top:387px;width:625px;height:58px;border:3px solid var(--sky);border-radius:8px;background:var(--navy-deep);display:flex;align-items:center;justify-content:center;font-size:32px;font-weight:700;white-space:nowrap}
  .stat-box .pct{color:var(--sky);font-weight:500;margin-right:8px}
  .ranking{position:absolute;left:0;top:467px;width:823px;text-align:center;color:var(--ink);font-size:24px;font-weight:800;line-height:27px}
  .ranking .accent{color:var(--sky)}
  .features{position:absolute;left:101px;top:543px;width:620px;height:156px}
  .features>svg{position:absolute;left:0;top:0}
  .features ul{position:absolute;left:33px;top:20px;list-style:none}
  .features li{display:flex;align-items:center;font-size:29px;font-weight:700;height:37.5px;white-space:nowrap}
  .features li svg{margin-right:16px;flex:none}
  .art-support{position:absolute;left:102px;top:722px;width:292px;height:205px;border-radius:14px;background:linear-gradient(160deg,#6fa6dc,#2c4fa3 60%,#1e2a6e)}
  .art-network{position:absolute;left:405px;top:692px;width:378px;height:200px;border-radius:14px;background:radial-gradient(ellipse at center,#3d4fa6,#262a72 75%)}
  .options-band{position:absolute;left:0;top:944px;width:823px;height:53px;background:linear-gradient(90deg,#2c4fa3,#2f57ad 60%,#4fa3de);display:flex;align-items:center;justify-content:center;font-size:24.5px;font-weight:700;white-space:nowrap}
  .footer{position:absolute;left:0;top:997px;width:823px;height:100px;background:var(--white);color:var(--ink)}
  .brand{position:absolute;left:64px;top:24px;width:129px;height:53px;border:2px solid var(--navy);display:flex;align-items:center;justify-content:center;font-size:34px;font-weight:700;color:var(--royal)}
  .contacts{position:absolute;left:208px;top:37px;display:flex;align-items:center;font-size:19px;font-weight:700;color:#1a1a2a;white-space:nowrap}
  .contacts .item{display:flex;align-items:center;gap:5px}
  .contacts .sep{margin:0 10px;color:var(--royal);font-weight:500}
</style>
</head>
<body>
<main class="flyer">
  <svg class="hero-bg" viewBox="0 0 823 422" aria-hidden="true">
    <defs>
      <linearGradient id="heroGrad" x1="0" y1="0" x2="1" y2="1">
        <stop offset="0" stop-color="#1a2350"/>
        <stop offset="0.5" stop-color="#161c42"/>
        <stop offset="1" stop-color="#1b2a5c"/>
      </linearGradient>
    </defs>
    <rect width="823" height="422" fill="url(#heroGrad)"/>
    <g stroke="#3a5aa8" stroke-opacity=".45" stroke-width="1.2" fill="none">
      <line x1="0" y1="180" x2="150" y2="20"/>
      <line x1="50" y1="0" x2="200" y2="150"/>
      <line x1="0" y1="420" x2="170" y2="250"/>
      <line x1="823" y1="60" x2="620" y2="260"/>
      <line x1="700" y1="0" x2="560" y2="150"/>
      <line x1="823" y1="300" x2="690" y2="422"/>
      <line x1="0" y1="280" x2="100" y2="380"/>
    </g>
    <polygon points="0,250 90,340 60,422 0,422" fill="#2a3f8a" opacity=".35"/>
    <polygon points="823,200 760,270 823,330" fill="#2a3f8a" opacity=".3"/>
  </svg>
  <div class="mid-band"></div>
  <div class="lower-bg"></div>

  <p class="tagline">YOUR CAREER IS JUST A <span class="accent"><svg viewBox="0 0 262 88" aria-hidden="true"><ellipse cx="131" cy="47" rx="126" ry="35" fill="none" stroke="#fff" stroke-width="1.6"/><path d="M62 10 Q146 -6 242 22" fill="none" stroke="#fff" stroke-width="1"/></svg>CLICK AWAY</span></p>

  <div class="title-box"><h1>DESKTOP &amp; NETWORK<br>SUPPORT COURSE</h1></div>

  <p class="subtitle">Master Skyline Operating Systems</p>

  <div class="stat-box"><span class="pct">90%</span> Employment Rate – Class of 2024</div>

  <p class="ranking">PREPARE FOR <span class="accent">3 OF THE TOP 10</span> TECH JOBS<br>NATIONAL CAREER &amp; JOBS REVIEW 2025</p>

  <section class="features">
    <svg width="620" height="156" viewBox="0 0 620 156" aria-hidden="true">
      <defs>
        <linearGradient id="featGrad" x1="0" y1="0" x2="1" y2="1">
          <stop offset="0" stop-color="#2a2f7e"/>
          <stop offset="0.6" stop-color="#3a42a0"/>
          <stop offset="1" stop-color="#2b3085"/>
        </linearGradient>
      </defs>
      <path d="M14 1 H606 Q619 1 619 14 V104 Q619 116 606 116 H350 Q338 116 330 126 L318 144 Q310 155 296 155 H14 Q1 155 1 142 V14 Q1 1 14 1 Z" fill="url(#featGrad)" stroke="#4f7fd0" stroke-width="2"/>
    </svg>
    <ul>
      <li><svg width="20" height="20" viewBox="0 0 20 20" aria-hidden="true"><circle cx="10" cy="10" r="10" fill="#4fa3de"/><path d="M5.5 10.3 L8.6 13.2 L14.5 7" fill="none" stroke="#2a2f7e" stroke-width="2.4"/></svg>Hands-On Desktop &amp; Network Training</li>
      <li><svg width="20" height="20" viewBox="0 0 20 20" aria-hidden="true"><circle cx="10" cy="10" r="10" fill="#4fa3de"/><path d="M5.5 10.3 L8.6 13.2 L14.5 7" fill="none" stroke="#2a2f7e" stroke-width="2.4"/></svg>Real-World Troubleshooting Skills</li>
      <li><svg width="20" height="20" viewBox="0 0 20 20" aria-hidden="true"><circle cx="10" cy="10" r="10" fill="#4fa3de"/><path d="M5.5 10.3 L8.6 13.2 L14.5 7" fill="none" stroke="#2a2f7e" stroke-width="2.4"/></svg>Ready for IT Jobs</li>
    </ul>
  </section>

  <div class="art-support" role="img" aria-label="Illustration of an IT support agent with headset on a computer screen, chat and rating bubbles, and two people beside a globe"></div>
  <div class="art-network" role="img" aria-label="Illustration of a network of connected user profile nodes"></div>

  <div class="options-band">In-Person and Remote Options Partial Scholarships Offered</div>

  <footer class="footer">
    <div class="brand">LOGO</div>
    <div class="contacts">
      <span class="item"><svg width="16" height="16" viewBox="0 0 16 16" aria-hidden="true"><circle cx="8" cy="8" r="8" fill="#2c4fa3"/><path d="M5 4 L6.8 4 L7.5 6 L6.5 7 Q7.5 9 9 9.6 L10 8.6 L12 9.3 V11 Q8.5 11.5 6 9 Q4 7 5 4 Z" fill="#fff"/></svg>123-456-7890</span>
      <span class="sep">|</span>
      <span class="item"><svg width="16" height="16" viewBox="0 0 16 16" aria-hidden="true"><circle cx="8" cy="8" r="8" fill="#2c4fa3"/><circle cx="8" cy="8" r="4.5" fill="none" stroke="#fff" stroke-width="1"/><ellipse cx="8" cy="8" rx="2" ry="4.5" fill="none" stroke="#fff" stroke-width="1"/><line x1="3.5" y1="8" x2="12.5" y2="8" stroke="#fff" stroke-width="1"/></svg>www.website.com</span>
      <span class="sep">|</span>
      <span class="item"><svg width="16" height="16" viewBox="0 0 16 16" aria-hidden="true"><circle cx="8" cy="8" r="8" fill="#2c4fa3"/><rect x="4" y="5" width="8" height="6" fill="none" stroke="#fff" stroke-width="1"/><path d="M4 5 L8 8.5 L12 5" fill="none" stroke="#fff" stroke-width="1"/></svg>info@mailbox.com</span>
    </div>
  </footer>
</main>
</body>
</html>
```